Website Design - TallyPorchHelpers.net

PLEASE CHECK WORD DOCUMENT ATTACHED FOR WEBSITE FLOW.

Target Market(s)

REAL ESTATE AGENTS ARE THE TARGET MARKET

Industry/Entity Type

Real Estate

Coding

Coded - Design and coding required

Number of Pages Required

4 page

Colors

Designer to choose colors to be used in the design.

Requirements
Must have
• WE LIKE RED LOGO ATTACHED
Nice to have
• PLEASE CHECK WORD DOCUMENT ATTACHED FOR WEBSITE FLOW.
Should not have

```html
<!DOCTYPE html>
<html lang="en">
<head>
<meta charset="utf-8">
<title>TallyPorchHelpers.net</title>
<link href="https://fonts.googleapis.com/css2?family=Poppins:ital,wght@0,400;0,500;0,600;0,700;1,400&family=Dancing+Script:wght@600&display=swap" rel="stylesheet">
<style>
:root{
  --red:#e41b23;
  --red-dark:#c5121a;
  --navy:#25288f;
  --navy-deep:#1e2170;
  --purple:#5a2a7a;
  --plum:#8a2856;
  --ink:#222;
  --muted:#666;
  --light:#f3f3f3;
  --white:#fff;
}
*{box-sizing:border-box;margin:0;padding:0}
html,body{width:1200px;height:4167px;overflow:hidden}
body{font-family:"Poppins",sans-serif;color:var(--ink);background:var(--white);position:relative}
section,header,footer{position:absolute;left:0;width:1200px}
.abs{position:absolute}
h2.section-title{position:absolute;left:0;width:1200px;text-align:center;font-size:24px;font-weight:700}

/* header */
.site-header{top:0;height:78px;background:var(--white)}
.brand{left:236px;top:18px;display:flex;align-items:center;gap:10px}
.brand-mark{width:40px;height:40px;background:var(--red);border-radius:6px}
.brand-name{font-weight:700;font-size:16px;color:var(--red);line-height:1.05}
.main-nav{left:388px;top:30px;display:flex;gap:30px;font-size:11px;font-weight:500;text-transform:uppercase;color:#333}
.header-call{left:838px;top:22px;display:flex;gap:8px;align-items:center}
.header-call .lbl{font-size:10px;color:#555;line-height:1.3}
.header-call .num{font-size:14px;font-weight:700;color:var(--red)}

/* hero */
.hero{top:78px;height:519px;background:linear-gradient(90deg,#c9302a 0%,#8c4a3c 40%,#4a4438 70%,#2d2a26 100%)}
.hero-photo{position:absolute;inset:0;background:linear-gradient(180deg,rgba(0,0,0,.05),rgba(0,0,0,.35)),linear-gradient(90deg,rgba(228,27,35,.75) 0%,rgba(180,60,50,.35) 35%,rgba(60,55,50,.2) 100%)}
.hero h1{position:absolute;top:210px;left:0;width:1200px;text-align:center;color:#fff;font-size:34px;font-weight:700}
.hero p{position:absolute;top:262px;left:0;width:1200px;text-align:center;color:#fff;font-size:17px;font-weight:500;line-height:1.4}

/* options */
.options{top:597px;height:236px;background:linear-gradient(180deg,var(--red) 0,var(--red) 193px,var(--light) 193px)}
.options h2{top:46px;color:#fff;font-size:22px}
.option-card{top:106px;width:225px;height:145px;background:#fff;border-radius:6px;box-shadow:0 8px 20px rgba(0,0,0,.15);text-align:center;padding-top:28px}
.option-card svg{display:block;margin:0 auto 12px}
.option-card span{display:block;font-size:12px;font-weight:600;line-height:1.35;text-transform:uppercase}
.option-card:after{content:"";position:absolute;left:0;right:0;bottom:0;height:5px;background:var(--red);border-radius:0 0 6px 6px}

/* how */
.how{top:833px;height:334px;background:var(--light)}
.how h2{top:62px}
.step{top:130px;width:220px;text-align:center}
.step-num{width:46px;height:46px;border-radius:50%;background:var(--navy);color:#fff;font-size:13px;font-weight:600;display:flex;align-items:center;justify-content:center;margin:0 auto 16px;box-shadow:0 0 0 5px #d7d8ee}
.step p{font-size:11px;line-height:1.55;color:#444}
.step-arrow{top:150px}

/* service area */
.service{top:1167px;height:161px;background:linear-gradient(90deg,var(--plum),var(--purple) 50%,var(--navy))}
.service h2{top:34px;color:#fff;font-size:22px}
.zip-form{left:361px;top:84px;display:flex}
.zip-form .field{width:376px;height:36px;background:#fff;font-size:11px;color:#999;padding:10px 14px}
.zip-form .btn{width:96px;height:36px;background:var(--red);color:#fff;font-size:11px;font-weight:600;display:flex;align-items:center;justify-content:center}
.map{top:1328px;height:422px;background:linear-gradient(135deg,#a8d4ef 0%,#a8d4ef 30%,#e8e4d8 45%,#efe9dc 100%)}

/* marketing */
.marketing{top:1750px;height:528px;background:linear-gradient(90deg,var(--navy) 0%,#4a2f8a 50%,var(--plum) 100%)}
.marketing-photo{position:absolute;right:0;top:0;width:492px;height:528px;background:linear-gradient(90deg,rgba(90,42,122,0) 0%,rgba(200,90,120,.55) 60%,rgba(230,120,130,.7) 100%)}
.marketing h2{left:236px;top:72px;font-size:22px;font-weight:700;color:#fff;position:absolute}
.service-item{width:225px;color:#fff}
.service-item .head{display:flex;align-items:center;gap:10px;font-size:14px;font-weight:600;text-transform:uppercase;margin-bottom:10px}
.service-item p{font-size:10.5px;line-height:1.6;opacity:.9}

/* packages */
.packages{top:2278px;height:611px;background:#f7f7f7}
.packages h2{top:62px}
.plan{top:111px;width:133px;height:470px;background:#fff;border-radius:4px;box-shadow:0 4px 14px rgba(0,0,0,.1);text-align:center}
.plan .name{height:48px;display:flex;align-items:center;justify-content:center;font-size:13px;font-weight:600;border-bottom:1px solid #eee}
.plan .price{width:52px;height:52px;border-radius:50%;background:var(--red);color:#fff;font-weight:700;font-size:17px;display:flex;align-items:center;justify-content:center;margin:14px auto 14px}
.plan .price sup{font-size:10px;margin-right:1px}
.plan ul{list-style:none;text-align:left;padding:0 12px;font-size:9.5px;line-height:1.5;color:#555}
.plan li{padding-left:14px;position:relative;margin-bottom:10px}
.plan li:before{content:"✓";position:absolute;left:0;color:var(--navy);font-weight:700}
.plan .cta{margin:16px auto 12px;width:104px;min-height:32px;padding:4px 6px;background:var(--navy);color:#fff;font-size:9px;font-weight:600;display:flex;align-items:center;justify-content:center;text-transform:uppercase;line-height:1.25}
.plan .note{font-size:8.5px;color:#888;padding:0 12px;line-height:1.4}
.plan.featured{top:100px;height:492px}
.plan.featured .name{background:var(--red);color:#fff;border-radius:4px 4px 0 0}
.plan.featured .price{background:var(--navy)}
.plan.featured .cta{background:var(--red)}

/* faq */
.faq{top:2889px;height:417px;background:linear-gradient(180deg,var(--plum) 0%,var(--purple) 45%,var(--navy) 100%)}
.faq h2{top:62px;color:#fff;font-size:22px}
.faq-item{width:347px;height:36px;background:#fff;font-size:11px;font-weight:500;display:flex;align-items:center;justify-content:space-between;padding:0 14px;color:#333}
.faq-item b{font-size:16px;font-weight:400;color:#777}
.faq-item.open{background:var(--red);color:#fff}
.faq-item.open b{color:#fff}
.faq-answer{width:353px;height:78px;background:#fff;font-size:9.5px;line-height:1.55;padding:8px 14px;color:#555}

/* testimonials */
.testimonials{top:3306px;height:505px;background:#fff}
.testimonials h2{top:72px}
.quote{width:350px;text-align:center}
.quote p{font-size:11px;line-height:1.6;color:#555;padding:0 30px}
.quote .mark{position:absolute;font-size:44px;font-weight:700;color:var(--red);line-height:1}
.quote .avatar{width:52px;height:52px;border-radius:50%;background:linear-gradient(135deg,#d8c8bc,#9c8a80);margin:30px auto 10px}
.quote .who{font-family:"Dancing Script",cursive;font-size:22px;color:#333}
.dots{top:3715px;left:560px;display:flex;gap:6px;position:absolute}
.dots i{width:7px;height:7px;border-radius:50%;background:#ccc;display:block}
.dots i.on{background:var(--red)}

/* newsletter + footer */
.newsletter-line{top:3809px;height:4px;background:var(--red)}
.newsletter-btn{position:absolute;top:3786px;left:439px;width:317px;height:48px;border-radius:24px;background:var(--red);color:#fff;font-size:13px;font-weight:600;display:flex;align-items:center;justify-content:center;gap:10px;text-transform:uppercase}
.site-footer{top:3813px;height:318px;background:var(--navy-deep);color:#fff}
.foot-col{top:80px}
.foot-col h4{font-size:12px;font-weight:600;text-transform:uppercase;margin-bottom:12px}
.foot-col p,.foot-col li{font-size:10px;line-height:1.75;opacity:.85;list-style:none}
.socials{display:flex;gap:6px;margin-top:12px}
.socials i{width:22px;height:22px;border:1px solid #fff;border-radius:50%;display:block}
.contact-form .in{width:166px;height:22px;background:#fff;margin-bottom:7px;font-size:9px;color:#999;padding:5px 8px}
.contact-form .msg{height:44px}
.contact-form .send{width:166px;height:26px;background:var(--red);font-size:9.5px;font-weight:600;display:flex;align-items:center;justify-content:center;text-transform:uppercase}
.bottom-bar{top:4131px;height:36px;background:#17195a;color:#fff;font-size:10px}
.bottom-bar span{position:absolute;top:11px}
</style>
</head>
<body>

<header class="site-header">
  <div class="brand abs"><div class="brand-mark"></div><div class="brand-name">Tally Porch<br>Helpers</div></div>
  <nav class="main-nav abs"><span>How it works</span><span>Service area</span><span>Pricing</span><span>About us</span><span>FAQ</span></nav>
  <div class="header-call abs">
    <svg width="26" height="26" viewBox="0 0 24 24"><path d="M6.6 10.8a15 15 0 006.6 6.6l2.2-2.2c.3-.3.7-.4 1-.2 1.1.4 2.3.6 3.6.6.6 0 1 .4 1 1V20c0 .6-.4 1-1 1A17 17 0 013 4c0-.6.4-1 1-1h3.5c.6 0 1 .4 1 1 0 1.3.2 2.5.6 3.6.1.3 0 .7-.2 1z" fill="#e41b23"/></svg>
    <div><div class="lbl">Call Or Text Us</div><div class="num">1-555-014-2290</div></div>
  </div>
</header>

<section class="hero">
  <div class="hero-photo" role="img" aria-label="Photo of two agents shaking hands outside a house with an open house sign"></div>
  <h1>Helping agents save time and money.</h1>
  <p>We place signs and boost foot traffic to your open houses<br>using proven marketing techniques.</p>
</section>

<section class="options">
  <h2 class="section-title">Choose The Option Below That Best Describes You</h2>
  <div class="option-card abs" style="left:236px">
    <svg width="34" height="34" viewBox="0 0 24 24"><path d="M3 21V7l6-4v4l6-4v4l6-4v18z" fill="#e41b23"/></svg>
    <span>I'm a<br>Full On Brokerage</span></div>
  <div class="option-card abs" style="left:486px">
    <svg width="34" height="34" viewBox="0 0 24 24"><circle cx="8" cy="8" r="3" fill="#e41b23"/><circle cx="16" cy="8" r="3" fill="#e41b23"/><path d="M2 19c0-3 3-5 6-5s6 2 6 5zM10 19c0-3 3-5 6-5s6 2 6 5z" fill="#e41b23"/></svg>
    <span>I'm an<br>Ind. Broker With A Team</span></div>
  <div class="option-card abs" style="left:735px">
    <svg width="34" height="34" viewBox="0 0 24 24"><path d="M4 2h2v20H4zM6 5h14v9H6z" fill="#e41b23"/></svg>
    <span>I Need<br>Sign Placement ASAP</span></div>
</section>

<section class="how">
  <h2 class="section-title">How It Works</h2>
  <div class="step abs" style="left:240px"><div class="step-num">01</div><p>We boost foot traffic to your open house using proven marketing channels: social ads, SMS notifications, voice broadcasts and email notifications</p></div>
  <svg class="step-arrow abs" style="left:470px" width="70" height="14" viewBox="0 0 70 14"><path d="M0 7h66M60 2l6 5-6 5" stroke="#333" fill="none"/></svg>
  <div class="step abs" style="left:490px"><div class="step-num">02</div><p>We place open house signs strategically in the surrounding area</p></div>
  <svg class="step-arrow abs" style="left:700px" width="70" height="14" viewBox="0 0 70 14"><path d="M0 7h66M60 2l6 5-6 5" stroke="#333" fill="none"/></svg>
  <div class="step abs" style="left:740px"><div class="step-num">03</div><p>Store custom signs for you if needed</p></div>
</section>

<section class="service">
  <h2 class="section-title">Service Area</h2>
  <div class="zip-form abs"><div class="field">Enter Your Open House Zip Code</div><div class="btn">SUBMIT</div></div>
</section>
<section class="map" role="img" aria-label="Map of the coastal service region with towns and highways"></section>

<section class="marketing">
  <div class="marketing-photo" role="img" aria-label="Photo of a woman shouting into a megaphone"></div>
  <h2>Marketing Services</h2>
  <div class="service-item abs" style="left:236px;top:133px">
    <div class="head"><svg width="30" height="30" viewBox="0 0 24 24"><circle cx="12" cy="12" r="10" fill="none" stroke="#fff" stroke-width="1.6"/><path d="M7 10h10M7 14h6" stroke="#fff" stroke-width="1.6"/></svg>SMS</div>
    <p>We will send a text message to all the people that live in the surrounding area of your open house to let them know there is a home for sale in their neighborhood and to let anyone that they may know looking to purchase a new home to come check it out!</p></div>
  <div class="service-item abs" style="left:481px;top:133px">
    <div class="head"><svg width="30" height="30" viewBox="0 0 24 24"><path d="M3 6h18v12H3zM3 6l9 7 9-7" fill="none" stroke="#fff" stroke-width="1.6"/></svg>Email</div>
    <p>We will send an email message to all the people that live in the surrounding area of your open house to let them know there is a home for sale in their neighborhood and to let anyone that they may know looking to purchase a new home to come check it out!</p></div>
  <div class="service-item abs" style="left:236px;top:314px">
    <div class="head"><svg width="30" height="30" viewBox="0 0 24 24"><rect x="3" y="3" width="18" height="18" rx="2" fill="none" stroke="#fff" stroke-width="1.6"/><path d="M8 16l4-5 4 5" fill="none" stroke="#fff" stroke-width="1.6"/></svg>Social Ads</div>
    <p>We will place a social ad to all the new hosts of all the people that live in the surrounding area of your open house to let them know there is a home for sale in their neighborhood and to let anyone that they may know looking to purchase a new home to come check it out!</p></div>
  <div class="service-item abs" style="left:481px;top:314px">
    <div class="head"><svg width="30" height="30" viewBox="0 0 24 24"><rect x="9" y="3" width="6" height="11" rx="3" fill="none" stroke="#fff" stroke-width="1.6"/><path d="M6 11a6 6 0 0012 0M12 17v4" fill="none" stroke="#fff" stroke-width="1.6"/></svg>Voice Broadcast</div>
    <p>We will send a voice broadcast to all the people that live in the surrounding area of your open house to let them know there is a home for sale in their neighborhood and to let anyone that they may know looking to purchase a new home to come check it out!</p></div>
</section>

<section class="packages">
  <h2 class="section-title">Choose Your Package</h2>
  <div class="plan abs" style="left:236px"><div class="name">5 SIGNS</div><div class="price"><sup>$</sup>49</div>
    <ul><li>Place signs strategically in best areas according to where the open house is located</li><li>Pick up the signs after the open house</li><li>Store custom signs for you if needed</li></ul>
    <span class="cta">Sign Up</span><div class="note">Sign up for a subscription and get three marketing services for free</div></div>
  <div class="plan abs" style="left:384px"><div class="name">10 SIGNS</div><div class="price"><sup>$</sup>59</div>
    <ul><li>Place signs strategically in best areas according to where the open house is located</li><li>Pick up the signs after the open house</li><li>Store custom signs for you if needed</li></ul>
    <span class="cta">Sign Up</span><div class="note">Sign up for a subscription and get three marketing services for free</div></div>
  <div class="plan featured abs" style="left:533px"><div class="name">15 SIGNS</div><div class="price"><sup>$</sup>69</div>
    <ul><li>Place signs strategically in best areas according to where the open house is located</li><li>Pick up the signs after the open house</li><li>Store custom signs for you if needed</li></ul>
    <span class="cta">Sign Up</span><div class="note">Sign up for a subscription and get three marketing services for free</div></div>
  <div class="plan abs" style="left:680px"><div class="name">20 SIGNS</div><div class="price"><sup>$</sup>79</div>
    <ul><li>Place signs strategically in best areas according to where the open house is located</li><li>Pick up the signs after the open house</li><li>Store custom signs for you if needed</li></ul>
    <span class="cta">Sign Up</span><div class="note">Sign up for a subscription and get three marketing services for free</div></div>
  <div class="plan abs" style="left:826px;width:138px"><div class="name">25+ SIGNS</div><div class="price"><sup>$</sup>—</div>
    <ul><li>Place signs strategically in best areas according to where the open house is located</li><li>Pick up the signs after the open house</li><li>Store custom signs for you if needed</li></ul>
    <span class="cta">Click Button To Create Custom Plan</span><div class="note">Sign up for a subscription and get three marketing services for free</div></div>
</section>

<section class="faq">
  <h2 class="section-title">Frequently Asked Questions</h2>
  <div class="faq-item abs" style="left:236px;top:131px">Vestibulum sed felis a ante suscipit auctor<b>+</b></div>
  <div class="faq-item abs" style="left:236px;top:178px">Sed ullamcorper augue ut facilisis condimentum<b>+</b></div>
  <div class="faq-item abs" style="left:236px;top:222px">Curabitur at ligula sed velit feugiat pellentesque<b>+</b></div>
  <div class="faq-item abs" style="left:236px;top:267px">Nam vitae velit non augue ultricies laoreet<b>+</b></div>
  <div class="faq-item abs" style="left:614px;top:131px">Curabitur at ligula sed velit feugiat pellentesque<b>+</b></div>
  <div class="faq-item open abs" style="left:614px;top:178px">Lorem ipsum used in various languages for layouts<b>−</b></div>
  <div class="faq-answer abs" style="left:611px;top:214px">In publishing and graphic design, lorem ipsum is a placeholder text commonly used to demonstrate the visual form of a document without relying on meaningful content. It fills a layout while the final copy is written.</div>
  <div class="faq-item abs" style="left:614px;top:302px">Sed ullamcorper augue ut facilisis condimentum<b>+</b></div>
  <div class="faq-item abs" style="left:614px;top:346px">Nam vitae velit non augue ultricies laoreet<b>+</b></div>
</section>

<section class="testimonials">
  <h2 class="section-title">Clients Testimonials</h2>
  <div class="quote abs" style="left:236px;top:134px">
    <span class="mark" style="left:0;top:-6px">“</span>
    <p>In publishing and graphic design, lorem ipsum is a placeholder text commonly used to demonstrate the visual form of a document. Lorem ipsum is a placeholder text commonly used to demonstrate the visual form of a document.</p>
    <span class="mark" style="right:0;top:90px">”</span>
    <div class="avatar" role="img" aria-label="Client portrait"></div>
    <div class="who">Marisol Keene</div></div>
  <div class="quote abs" style="left:614px;top:134px">
    <span class="mark" style="left:0;top:-6px">“</span>
    <p>In publishing and graphic design, lorem ipsum is a placeholder text commonly used to demonstrate the visual form of a document. Lorem ipsum is a placeholder text commonly used to demonstrate the visual form of a document.</p>
    <span class="mark" style="right:0;top:90px">”</span>
    <div class="avatar" role="img" aria-label="Client portrait"></div>
    <div class="who">Dorian Vale</div></div>
</section>
<div class="dots"><i></i><i></i><i class="on"></i><i></i><i></i></div>

<footer class="site-footer">
  <div class="foot-col abs" style="left:236px;width:200px"><h4>About Tally Porch Helpers</h4>
    <p>Started and operated by a highly experienced agent and top realtor, we help agents leverage their time and skills to increase production at an affordable price with impeccable support.</p>
    <div class="socials"><i></i><i></i><i></i><i></i><i></i></div></div>
  <div class="foot-col abs" style="left:467px;width:190px"><h4>Contact Information</h4>
    <p>4120 Maple Grove Drive<br>Suite 210, Fairfield, TX 75000</p><p style="margin-top:6px">Call Or Text Us:<br>1-555-014-2290</p><p style="margin-top:6px">Email Us:<br>hello@tallyporchhelpers.net</p></div>
  <div class="foot-col abs" style="left:675px"><h4>Quick Links</h4>
    <ul><li>How It Works</li><li>Service Area</li><li>Pricing</li><li>About Us</li><li>FAQ</li></ul></div>
  <div class="foot-col contact-form abs" style="left:797px"><h4>Contact Us Right Now</h4>
    <div class="in">Name</div><div class="in">Email</div><div class="in">Phone</div><div class="in msg">Message</div><div class="send">Send A Message</div></div>
</footer>
<div class="newsletter-line abs" style="left:0;width:1200px"></div>
<div class="newsletter-btn"><svg width="22" height="16" viewBox="0 0 24 16"><path d="M1 8L23 1 17 15 12 10z" fill="none" stroke="#fff" stroke-width="1.6"/></svg>Subscribe To Our Newsletter</div>
<div class="bottom-bar abs" style="left:0;width:1200px">
  <span style="left:236px">Copyright © 2018 TallyPorchHelpers.net</span>
  <span style="left:815px">Terms of Use / Privacy / Sitemap</span>
</div>

</body>
</html>
```